SOLVE Study flyer

I need help designing a flyer for a research study that will include brain imaging in adolescents. The info is in the attached document. The study is called the Sequoia Outlook Lantern Valley Echo (SOLVE) study. Ideally this would be returned as a document that I can edit in the future as we will have several new recruitment phases (different age groups, etc. I also would love to have a logo designed as part of this project, but I recognize that might be a separate design request.

```html
<!DOCTYPE html>
<html lang="en">
<head>
<meta charset="utf-8">
<title>SOLVE Study – Recruitment Flyer</title>
<link href="https://fonts.googleapis.com/css2?family=Figtree:wght@400;500;600;700;800&display=swap" rel="stylesheet">
<style>
  :root {
    --navy: #13205e;
    --navy-deep: #0f1a4d;
    --teal: #1a9aa0;
    --teal-bright: #2bb7b8;
    --purple: #7a4fc4;
    --purple-soft: #a584ec;
    --lilac-card: #f5f2fc;
    --mint-card: #f2f8f9;
    --blue-card: #eff3fb;
    --ink: #14204f;
    --line: #cfd6ee;
    --gold: #f6c34c;
    --white: #ffffff;
  }
  * { box-sizing: border-box; margin: 0; padding: 0; }
  html, body { width: 840px; height: 1200px; overflow: hidden; background: var(--white); }
  body { font-family: "Figtree", Arial, sans-serif; color: var(--ink); }
  .flyer { position: relative; width: 840px; height: 1200px; overflow: hidden; background: var(--white); }

  .hero-band, .hero-photo { position: absolute; left: 0; top: 0; width: 840px; height: 560px; }

  /* Header */
  .brand { position: absolute; left: 66px; top: 26px; display: flex; align-items: flex-start; gap: 20px; }
  .brand-mark { width: 80px; height: 80px; border-radius: 50%; background: var(--teal); margin-top: 14px; flex: none; }
  .brand-name { font-size: 58px; font-weight: 800; line-height: 1; color: var(--navy); letter-spacing: 0.5px; }
  .brand-sub { font-size: 22px; font-weight: 700; color: var(--teal); letter-spacing: 8px; line-height: 1; margin-top: 8px; }
  .brand-full { font-size: 14px; font-weight: 500; color: var(--navy); margin-top: 8px; line-height: 18px; white-space: nowrap; }
  .header-divider { position: absolute; left: 407px; top: 41px; width: 1px; height: 108px; background: var(--line); }
  .institution { position: absolute; left: 446px; top: 44px; display: flex; gap: 17px; }
  .institution-mark { width: 66px; height: 66px; background: var(--navy); flex: none; }
  .institution-name { font-size: 24px; font-weight: 700; color: var(--navy); line-height: 25px; margin-top: 6px; }
  .institution-dept { font-size: 13px; font-weight: 500; color: var(--navy); line-height: 19px; margin-top: 8px; }

  /* Hero copy */
  .hero-copy { position: absolute; left: 35px; top: 200px; color: var(--white); }
  .hero-lead { font-size: 35px; font-weight: 700; line-height: 44px; letter-spacing: -0.3px; }
  .hero-age { font-size: 51px; font-weight: 800; color: var(--teal-bright); line-height: 56px; letter-spacing: -0.8px; }
  .hero-rule { width: 291px; height: 3px; background: var(--purple-soft); margin: 19px 0 16px; }
  .hero-question { font-size: 29px; font-weight: 700; line-height: 37px; letter-spacing: -0.3px; }

  /* Intro card */
  .intro-card { position: absolute; left: 41px; top: 437px; width: 671px; height: 139px;
    background: var(--white); border: 1.5px solid var(--line); border-radius: 16px; }
  .intro-icon { position: absolute; left: 33px; top: 6px; width: 124px; height: 124px; border-radius: 50%; background: #eef4f6; }
  .intro-text { position: absolute; left: 195px; top: 16px; font-size: 17.5px; font-weight: 500; line-height: 27px; white-space: nowrap; }
  .intro-text strong { color: var(--purple); font-weight: 700; }

  /* Steps */
  .section-title { position: absolute; left: 41px; top: 593px; width: 761px; display: flex; align-items: center; gap: 16px;
    font-size: 24px; line-height: 30px; font-weight: 700; color: var(--navy); white-space: nowrap; }
  .section-title::before, .section-title::after { content: ""; flex: 1; height: 2px; background: var(--teal); }
  .steps { position: absolute; left: 41px; top: 631px; width: 761px; height: 226px; display: flex; gap: 16px; }
  .step { position: relative; border: 1px solid #e4e8f3; border-radius: 12px; padding: 0 8px;
    display: flex; flex-direction: column; align-items: center; text-align: center;
    font-size: 15px; font-weight: 500; line-height: 20px; }
  .step--interview { width: 229px; background: var(--lilac-card); }
  .step--survey { width: 207px; background: var(--mint-card); }
  .step--scan { flex: 1; background: var(--blue-card); }
  .step-number { position: absolute; left: 10px; top: 5px; width: 36px; height: 36px; border-radius: 50%;
    color: var(--white); font-weight: 700; font-size: 21px; display: flex; align-items: center; justify-content: center; }
  .step--interview .step-number { background: var(--purple); }
  .step--survey .step-number { background: var(--teal); }
  .step--scan .step-number { background: #1f3f9c; }
  .step--interview .step-icon { margin-top: 12px; width: 100px; height: 85px; }
  .step--survey .step-icon { margin-top: 12px; width: 76px; height: 89px; }
  .step--scan .step-icon { margin-top: 8px; width: 131px; height: 89px; }
  .step--interview p { margin-top: 14px; }
  .step--survey p { margin-top: 26px; }
  .step--scan p { margin-top: 4px; line-height: 19.5px; }

  /* Eligibility */
  .family-photo { position: absolute; left: 0; top: 870px; width: 365px; height: 216px;
    background: linear-gradient(120deg, #ece7e2 0%, #cbbcc8 42%, #9d86c4 72%, #7c67b4 100%);
    border-right: 8px solid var(--teal); border-top: 3px solid var(--purple); border-radius: 0 120px 0 0; }
  .eligibility { position: absolute; left: 411px; top: 871px; width: 367px; }
  .eligibility h2 { font-size: 21px; line-height: 24px; font-weight: 700; color: var(--teal); margin-bottom: 16px; white-space: nowrap; }
  .criteria { list-style: none; }
  .criteria li { display: flex; align-items: center; gap: 7px; font-size: 15px; font-weight: 500; line-height: 19px; }
  .criteria li:nth-child(1) { height: 34px; }
  .criteria li:nth-child(2) { height: 40px; }
  .criteria li:nth-child(3) { align-items: flex-start; padding-top: 10px; }
  .criteria li + li { border-top: 1px dashed #8fcbcf; margin-left: 36px; }
  .criteria li + li .tick { margin-left: -36px; }
  .tick { flex: none; width: 29px; height: 29px; }
  .criteria li:nth-child(3) .tick { margin-top: 3px; }

  /* Contact */
  .contact { position: absolute; left: 33px; top: 1048px; width: 775px; height: 150px; border-radius: 20px;
    background: linear-gradient(90deg, var(--navy-deep) 0%, #1e2b7a 58%, #5a3ea8 100%); }
  .contact-icon { position: absolute; left: 26px; top: 25px; width: 90px; height: 90px; border-radius: 50%;
    background: var(--purple); border: 3px solid var(--white); display: flex; align-items: center; justify-content: center; }
  .contact-copy { position: absolute; left: 134px; top: 13px; color: var(--white); font-size: 20px; font-weight: 700; line-height: 28px; white-space: nowrap; }
  .contact-copy .cta { color: var(--purple-soft); margin-top: 5px; display: flex; align-items: flex-end; }
  .contact-copy .cta::after { content: ""; width: 115px; height: 1.5px; background: var(--white); margin: 0 0 6px 10px; }
  .contact-email { font-size: 25px; font-weight: 600; line-height: 30px; margin-top: 3px; }
  .contact-divider { position: absolute; left: 488px; top: 16px; height: 113px; border-left: 1.5px dashed rgba(255,255,255,0.5); }
  .reward { position: absolute; left: 561px; top: -14px; width: 165px; height: 165px; border-radius: 50%;
    background: var(--gold); border: 3px solid #fbe3a1; color: var(--navy); text-align: center;
    display: flex; flex-direction: column; align-items: center; justify-content: center; }
  .reward-label { font-size: 15.5px; font-weight: 600; line-height: 19px; margin-top: 4px; }
  .reward-amount { font-size: 45px; font-weight: 800; line-height: 1; letter-spacing: -0.5px; }
</style>
</head>
<body>
<main class="flyer">

  <svg class="hero-band" viewBox="0 0 840 560" aria-hidden="true">
    <path d="M0 130 C150 170 300 185 420 185 C560 185 700 160 840 125 L840 530 C620 522 330 470 0 490 Z" fill="#13205e"/>
  </svg>
  <svg class="hero-photo" viewBox="0 0 840 560" role="img" aria-label="Photo of a thoughtful teenage girl with a glowing brain graphic and an MRI scanner">
    <defs>
      <clipPath id="hero-clip">
        <path d="M397 183 C560 185 700 160 840 125 L840 530 C700 526 560 512 397 500 Z"/>
      </clipPath>
      <linearGradient id="hero-fade" x1="0" y1="0" x2="1" y2="0">
        <stop offset="0" stop-color="#13205e"/>
        <stop offset="0.3" stop-color="#3a3a8e"/>
        <stop offset="0.65" stop-color="#7a5cb8"/>
        <stop offset="1" stop-color="#b8bfd6"/>
      </linearGradient>
      <radialGradient id="hero-glow" cx="0.8" cy="0.25" r="0.4">
        <stop offset="0" stop-color="#6a7cf0" stop-opacity="0.9"/>
        <stop offset="1" stop-color="#6a7cf0" stop-opacity="0"/>
      </radialGradient>
    </defs>
    <g clip-path="url(#hero-clip)">
      <rect x="397" y="100" width="443" height="440" fill="url(#hero-fade)"/>
      <rect x="397" y="100" width="443" height="440" fill="url(#hero-glow)"/>
    </g>
  </svg>

  <header>
    <div class="brand">
      <div class="brand-mark"></div>
      <div>
        <div class="brand-name">SOLVE</div>
        <div class="brand-sub">STUDY</div>
        <div class="brand-full">Sequoia Outlook Lantern Valley<br>Echo</div>
      </div>
    </div>
    <div class="header-divider"></div>
    <div class="institution">
      <div class="institution-mark"></div>
      <div>
        <div class="institution-name">Ridgeview<br>University</div>
        <div class="institution-dept">School of Medicine<br>Department of Psychiatry</div>
      </div>
    </div>
  </header>

  <section class="hero-copy">
    <div class="hero-lead">Are you the parent of</div>
    <div class="hero-age">a child age 10-17?</div>
    <div class="hero-rule"></div>
    <div class="hero-question">Do they worry or overthink<br>negative emotions?</div>
  </section>

  <section class="intro-card">
    <div class="intro-icon" role="img" aria-label="Brain illustration"></div>
    <p class="intro-text">Ridgeview University researchers are seeking<br><strong>girls age 10-17</strong> for a study about brain activity in<br>emotions and decision-making and how they<br>relate to puberty, anxiety and depression.</p>
  </section>

  <h2 class="section-title">Study participation involves:</h2>
  <section class="steps">
    <div class="step step--interview">
      <span class="step-number">1</span>
      <svg class="step-icon" viewBox="0 0 80 68" fill="none" stroke="#7a4fc4" stroke-width="2.2" aria-hidden="true">
        <circle cx="18" cy="30" r="8"/><path d="M4 64 C4 50 32 50 32 64"/>
        <circle cx="58" cy="40" r="7"/><path d="M45 64 C45 53 71 53 71 64"/>
        <rect x="36" y="4" width="40" height="22" rx="4"/><path d="M44 26 L42 34 L52 26"/>
        <path d="M43 12 H68 M43 18 H62"/>
        <path d="M14 64 H40"/>
      </svg>
      <p>One 1-hour interview<br>(online or in-person)<br>where your child will<br>discuss their thoughts</p>
    </div>
    <div class="step step--survey">
      <span class="step-number">2</span>
      <svg class="step-icon" viewBox="0 0 60 70" fill="none" stroke="#1a9aa0" stroke-width="2.2" aria-hidden="true">
        <rect x="6" y="8" width="48" height="60" rx="4"/>
        <rect x="20" y="3" width="20" height="10" rx="3"/>
        <path d="M13 26 l4 4 l6 -7 M28 27 H46 M13 40 l4 4 l6 -7 M28 41 H46 M13 54 l4 4 l6 -7 M28 55 H46"/>
      </svg>
      <p>Online questionnaires<br>(parent and child)</p>
    </div>
    <div class="step step--scan">
      <span class="step-number">3</span>
      <svg class="step-icon" viewBox="0 0 130 88" fill="none" stroke="#1f3f9c" stroke-width="2.2" aria-hidden="true">
        <path d="M60 86 V36 C60 12 76 2 92 2 C108 2 124 12 124 36 V86 Z"/>
        <circle cx="92" cy="44" r="22"/>
        <path d="M6 64 H104 V72 H6 Z M20 72 V86 M84 72 V86"/>
        <circle cx="84" cy="56" r="6"/>
        <path d="M30 64 C34 54 62 52 78 58"/>
      </svg>
      <p>One 2-hour visit where<br>your child will complete an<br>MRI scan, answer questions<br>about their puberty stage,<br>and have a small hair sample<br>taken to study puberty hormones</p>
    </div>
  </section>

  <div class="family-photo" role="img" aria-label="Photo of a mother smiling at her teenage daughter"></div>

  <section class="eligibility">
    <h2>Your child may be eligible if they:</h2>
    <ul class="criteria">
      <li><svg class="tick" viewBox="0 0 22 22" aria-hidden="true"><circle cx="11" cy="11" r="11" fill="#1a9aa0"/><path d="M6 11 l3.5 3.5 L16 8" fill="none" stroke="#fff" stroke-width="2.4"/></svg><span>Are age 10-17</span></li>
      <li><svg class="tick" viewBox="0 0 22 22" aria-hidden="true"><circle cx="11" cy="11" r="11" fill="#1a9aa0"/><path d="M6 11 l3.5 3.5 L16 8" fill="none" stroke="#fff" stroke-width="2.4"/></svg><span>Tend to worry or overthink negative thoughts</span></li>
      <li><svg class="tick" viewBox="0 0 22 22" aria-hidden="true"><circle cx="11" cy="11" r="11" fill="#1a9aa0"/><path d="M6 11 l3.5 3.5 L16 8" fill="none" stroke="#fff" stroke-width="2.4"/></svg><span>Have not been diagnosed with psychosis,<br>learning problems, or autism</span></li>
    </ul>
  </section>

  <section class="contact">
    <div class="contact-icon">
      <svg width="48" height="34" viewBox="0 0 38 28" fill="none" stroke="#fff" stroke-width="2.4" aria-hidden="true">
        <rect x="2" y="2" width="34" height="24" rx="3"/><path d="M3 4 L19 16 L35 4"/>
      </svg>
    </div>
    <div class="contact-copy">
      <div>Interested in participating?</div>
      <div>Want more information?</div>
      <div class="cta">Please contact us!</div>
      <div class="contact-email">solvestudy@ridgeview.edu</div>
    </div>
    <div class="contact-divider"></div>
    <div class="reward">
      <svg width="34" height="34" viewBox="0 0 26 26" aria-hidden="true">
        <rect x="2" y="9" width="22" height="6" fill="#13205e"/><rect x="4" y="15" width="18" height="10" fill="#13205e"/>
        <rect x="12" y="9" width="2" height="16" fill="#f6c34c"/>
        <path d="M13 9 C8 2 4 6 8 9 M13 9 C18 2 22 6 18 9" fill="none" stroke="#13205e" stroke-width="2"/>
      </svg>
      <div class="reward-label">Compensation<br>up to</div>
      <div class="reward-amount">$140</div>
    </div>
  </section>

</main>
</body>
</html>
```